GJ & DW Fencing Pty Ltd

We already have an existing logo created by Pixel Harbour however we have restructured to a company. We would like someone to add Pty Ltd to our business name please.

Colors

Designer to choose only greyscale colors for use in the design.

```html
<!DOCTYPE html>
<html lang="en">
<head>
<meta charset="utf-8">
<title>GJ &amp; DW Fencing Pty Ltd — Business Card</title>
<link rel="stylesheet" href="https://fonts.googleapis.com/css2?family=Noto+Serif:wght@400;700&display=swap">
<style>
  :root {
    --page-bg: #2b2b2d;
    --card-bg: #1f2123;
    --card-edge: #34373a;
    --ink: #f2f2f2;
    --ink-soft: #c9c9c9;
  }
  * { box-sizing: border-box; margin: 0; padding: 0; }
  html, body { width: 1200px; height: 800px; overflow: hidden; }
  body {
    background: var(--page-bg);
    font-family: "Noto Serif", Georgia, serif;
    color: var(--ink);
    display: flex;
    align-items: center;
    justify-content: center;
    gap: 48px;
  }
  .card {
    position: relative;
    width: 520px;
    height: 300px;
    background: var(--card-bg);
    border: 1px solid var(--card-edge);
    border-radius: 22px;
    box-shadow: 0 18px 40px rgba(0,0,0,0.45);
  }
  .brand {
    display: flex;
    align-items: center;
    gap: 12px;
    font-weight: 700;
    color: var(--ink);
    white-space: nowrap;
  }
  .brand-dot {
    width: 14px; height: 14px;
    border-radius: 50%;
    background: var(--ink);
    flex: none;
  }
  .card-front .brand {
    position: absolute;
    top: 50%; left: 50%;
    transform: translate(-50%, -50%);
    font-size: 30px;
  }
  .card-back .brand {
    position: absolute;
    top: 70px; right: 40px;
    font-size: 24px;
  }
  .contact {
    position: absolute;
    left: 40px; bottom: 34px;
    font-size: 12.5px;
    line-height: 1.55;
    color: var(--ink-soft);
  }
  .contact-name {
    font-weight: 700;
    font-size: 15px;
    letter-spacing: 0.06em;
    color: var(--ink);
  }
  .contact-role { margin-bottom: 10px; }
  .contact-line { display: flex; align-items: center; gap: 8px; }
  .contact-icon { width: 16px; height: 16px; flex: none; }
  .contact-company { font-weight: 700; color: var(--ink); margin-top: 6px; }
</style>
</head>
<body>
  <section class="card card-front" aria-label="Card front">
    <div class="brand"><span class="brand-dot"></span>GJ &amp; DW Fencing Pty Ltd</div>
  </section>

  <section class="card card-back" aria-label="Card back">
    <div class="brand"><span class="brand-dot"></span>GJ &amp; DW Fencing Pty Ltd</div>
    <div class="contact">
      <p class="contact-name">LIAM CARTER</p>
      <p class="contact-role">President</p>
      <p class="contact-line">
        <svg class="contact-icon" viewBox="0 0 16 16" aria-hidden="true">
          <circle cx="8" cy="8" r="8" fill="#f2f2f2"/>
          <rect x="5.5" y="3.5" width="5" height="9" rx="1" fill="#1f2123"/>
          <rect x="6.5" y="4.8" width="3" height="5.5" fill="#f2f2f2"/>
        </svg>
        Tom 0491570110
      </p>
      <p class="contact-line">
        <svg class="contact-icon" viewBox="0 0 16 16" aria-hidden="true">
          <circle cx="8" cy="8" r="8" fill="#f2f2f2"/>
          <rect x="4" y="5" width="8" height="6" rx="0.8" fill="#1f2123"/>
          <path d="M4.5 5.6 L8 8.4 L11.5 5.6" stroke="#f2f2f2" stroke-width="0.9" fill="none"/>
        </svg>
        gjdwfencing@mailbox.com
      </p>
      <p class="contact-company">GJ &amp; DW Fencing Pty Ltd</p>
      <p>PO Box 215 Brookvale WA 6300</p>
    </div>
  </section>
</body>
</html>
```